Flat Belly Design Graphics for Social

I want to create 9 social media graphics (new Instagram size 4:5 (1080 x 1350 pixels) focusing on our Flat Belly Graphics, using the pics attached. Use the attached pics, NO RANDOM STOCK PHOTOGRAPHY. For the color scheme of the graphics, the color palette is attached. YOU MUST POST ALL 9 GRAPHICS IN ONE ENTRY.
Using the 3 titles below, create one set of graphics. 1) with all text, then for the others, use the pictures as detailed below in IMPORTANT:
1. Ten-Week Bright Morning Reboot
2. The Quick Garden Kitchen Menu Guide
3. Studio Habits for Lasting Energy Past Midlife - Zero Gym Needed
IMPORTANT:
Only use RK Pic 1 and RK Pic 2 with the title, Ten-Week Bright Morning Reboot
Only use meal plan1 and meal plan2 pics with the title, Quick Garden Kitchen Menu Guide
Only use studio habits 1 and studio habits 2 pics with the title, Studio Habits for Lasting Energy Past Midlife - Zero Gym Needed
women over 40

```html
<!DOCTYPE html>
<html lang="en">
<head>
<meta charset="utf-8">
<title>Morning Reboot Social Set</title>
<link href="https://fonts.googleapis.com/css2?family=Bebas+Neue&family=Russo+One&display=swap" rel="stylesheet">
<style>
:root{
  --bg:#1f0008;
  --card:#fbeef0;
  --green:#2f4a45;
  --pink:#b84f6c;
  --rose-line:#e8a0b0;
  --rose-band:#f3c0cf;
  --rose-block:#e296ad;
  --white:#ffffff;
}
*{margin:0;padding:0;box-sizing:border-box}
html,body{width:1077px;height:1200px;overflow:hidden;background:var(--bg)}
.canvas{position:relative;width:1077px;height:1200px}
.post{position:absolute;width:207px;height:258px;background:var(--card);overflow:hidden;
  font-family:"Bebas Neue",sans-serif;text-align:center;line-height:.92}
.col-a{left:215px}.col-b{left:435px}.col-c{left:655px}
.row-1{top:194px}.row-2{top:469px}.row-3{top:746px}
.frame{position:absolute;inset:13px;border:1px solid var(--rose-line);pointer-events:none}
.stack{position:absolute;inset:13px;display:flex;flex-direction:column;justify-content:center;align-items:center}
.dark{color:var(--green)}.pink{color:var(--pink)}.light{color:var(--white)}.soft{color:var(--rose-block)}
.photo{position:absolute;left:0;right:0;top:0}
.caption{position:absolute;left:0;right:0;bottom:0;display:flex;flex-direction:column;justify-content:center;align-items:center}
.heavy{font-family:"Russo One",sans-serif;line-height:1.1}
</style>
</head>
<body>
<main class="canvas">

  <!-- Row 1: type only -->
  <section class="post col-a row-1">
    <div class="frame"></div>
    <div class="stack">
      <div class="dark" style="font-size:40px">Ten-Week</div>
      <div class="pink" style="font-size:62px">Bright</div>
      <div class="pink" style="font-size:46px">Morning</div>
      <div class="dark" style="font-size:32px">Reboot</div>
    </div>
  </section>

  <section class="post col-b row-1">
    <div class="frame"></div>
    <div class="stack">
      <div class="dark" style="font-size:24px">The Quick</div>
      <div class="pink" style="font-size:58px">Garden</div>
      <div class="pink" style="font-size:52px">Kitchen</div>
      <div class="dark" style="font-size:34px">Menu Guide</div>
    </div>
  </section>

  <section class="post col-c row-1">
    <div class="frame"></div>
    <div class="stack">
      <div class="dark" style="font-size:44px">Studio</div>
      <div class="dark" style="font-size:34px">Habits for</div>
      <div class="pink" style="font-size:30px">Lasting Energy</div>
      <div class="pink" style="font-size:34px">Past Midlife</div>
      <div class="dark" style="font-size:20px">Zero Gym Needed</div>
    </div>
  </section>

  <!-- Row 2: photo top, framed type -->
  <section class="post col-a row-2">
    <div class="photo" role="img" aria-label="Morning reboot photo 1: smiling woman in a white cropped sweater pointing at her waist"
      style="top:13px;left:13px;right:13px;height:133px;background:linear-gradient(to bottom,var(--card) 0 28%,transparent 28%),linear-gradient(90deg,#fbe4ea,var(--rose-band) 20%,var(--rose-band) 80%,#fbe4ea)"></div>
    <div class="frame"></div>
    <div class="caption" style="top:146px;bottom:13px">
      <div class="dark" style="font-size:30px">Ten-Week</div>
      <div class="dark" style="font-size:28px">Bright Morning</div>
      <div class="pink" style="font-size:22px">Reboot</div>
    </div>
  </section>

  <section class="post col-b row-2">
    <div class="frame"></div>
    <div class="photo" role="img" aria-label="Menu guide photo 1: notepad menu plan surrounded by fresh produce, fish and chicken"
      style="height:137px;background:radial-gradient(circle at 50% 50%,#4a3324 0 30%,#6b5a2e 55%,#8a3b2a 100%)"></div>
    <div class="caption" style="top:137px;bottom:13px">
      <div class="dark" style="font-size:26px">The Quick Garden</div>
      <div class="dark" style="font-size:28px">Kitchen Menu</div>
      <div class="pink" style="font-size:22px">Guide</div>
    </div>
  </section>

  <section class="post col-c row-2">
    <div class="frame"></div>
    <div class="photo" role="img" aria-label="Studio habits photo 1: two women sharing a whispered secret, one looking surprised"
      style="height:142px;background:linear-gradient(135deg,#e8e4e2,#c9a48f 55%,#f0eeed)"></div>
    <div class="caption" style="top:142px;bottom:13px">
      <div class="dark" style="font-size:21px">Studio Habits for</div>
      <div class="dark" style="font-size:21px">Lasting Energy</div>
      <div class="dark" style="font-size:21px">Past Midlife</div>
      <div class="pink" style="font-size:18px">Zero Gym Needed</div>
    </div>
  </section>

  <!-- Row 3: full photo with colour band -->
  <section class="post col-a row-3">
    <div class="photo" role="img" aria-label="Morning reboot photo 2: smiling woman in a white cropped sweater in a kitchen pointing at her waist"
      style="bottom:0;background:linear-gradient(180deg,#6e5548,#a47b61 55%,#3a2d28)"></div>
    <div class="caption" style="top:167px;background:rgba(47,74,69,.94)">
      <div class="heavy light" style="font-size:17px">TEN-WEEK BRIGHT</div>
      <div class="soft" style="font-size:22px;margin-top:4px">Morning Reboot</div>
    </div>
  </section>

  <section class="post col-b row-3">
    <div class="photo" role="img" aria-label="Menu guide photo 2: menu sheet with chicken, berries, asparagus and grains"
      style="bottom:0;background:linear-gradient(180deg,#8a5a40,#6b4a34 45%,var(--rose-block) 58%)"></div>
    <div class="caption" style="top:128px">
      <div class="heavy light" style="font-size:17px">THE QUICK GARDEN</div>
      <div class="heavy light" style="font-size:19px">KITCHEN MENU</div>
      <div class="dark" style="font-size:22px;margin-top:4px">Guide</div>
    </div>
  </section>

  <section class="post col-c row-3">
    <div class="photo" role="img" aria-label="Studio habits photo 2: two women against a blue wall, one whispering to the other"
      style="bottom:0;background:linear-gradient(180deg,#6ec6d8,#8fb9c4 60%,#5d8e94)"></div>
    <div class="caption" style="top:163px;background:rgba(47,74,69,.9)">
      <div class="heavy light" style="font-size:14px">STUDIO HABITS FOR</div>
      <div class="heavy light" style="font-size:14px">LASTING ENERGY PAST MIDLIFE</div>
      <div class="soft" style="font-size:20px;margin-top:4px">Zero Gym Needed</div>
    </div>
  </section>

</main>
</body>
</html>
```